Business card design needed

Family General Practitioner/ Family Physician.
Logo is the logo of the Noble Guild of Family Healers Oceania
http://kpltw.varendo.example/ImageShelf/marks/pages/NGFHO%20mark_jpg.htm
Updates

Project Deadline Extended
Reason: Just a bit more time to make changes and the weekend for me to look at things closely and to choose. Thanks, Orin

Thanks for all the submissions. So many of them are really works of art. Not one of them are not good. The ones that I am eliminating are the ones that I think are not suitable for me personally only, and because if I don't, it makes it very difficult to decide as many of you are also sending me slight variations of a card. I have just decided to choose a second place card too. Can't thank you all enough. Good luck, Orin. P.S - Working today till 10 pm as the card says :-), so probably won't be able to give a feedback till late Saturday night or Sunday morning here in Sydney, Australia. 

Project Deadline Extended
Reason: Just added a second place to the budget and realised that Australia is ahead of the rest of the world in the time zone (only :-) - don't want to offend anyone or start a debate!! ) , so Monday deadline will mean it will be a weekend for the rest of the world. Just wanted to give everyone more time to submit their best, especially since I will be picking a second card too. Can't thank everyone enough for the submissions. P.S - Not keen on photos on the card.

Industry/Entity Type

Business

Contact Information for Business Card

Dr. Orin Halvey M.B.B.S., F.N.G.F.H.O
Family General Practitioner
Address, timings, phone and fax number on the back.

Requirements
Must have
• Timings
Mon 7 am - 7 pm
Tues 7 am - 12 pm
Wed 7 am - 10 pm
Thurs 7 am - 12 pm
Fri 7 am - 8 pm
Sat 8 am - 10 pm
Sun - Off

```html
<!DOCTYPE html>
<html lang="en">
<head>
<meta charset="utf-8">
<title>Dr. Orin Halvey – Business Card Options</title>
<link rel="stylesheet" href="https://fonts.googleapis.com/css2?family=Cinzel:wght@500&family=Open+Sans:wght@400&family=Tinos:wght@400;700&display=swap">
<style>
  :root {
    --stage: #b3845a;
    --navy-light: #3f5d8c;
    --navy: #31456b;
    --navy-dark: #283550;
    --crimson: #8a2327;
    --crimson-dark: #5c2a26;
    --gold: #c9a24a;
    --sage: #8fa45a;
    --rule: #7d8594;
    --white: #ffffff;
    --ink-soft: rgba(255,255,255,0.92);
  }
  * { box-sizing: border-box; margin: 0; padding: 0; }
  html, body { width: 1200px; height: 775px; overflow: hidden; }
  body { background: var(--stage); position: relative; font-family: "Open Sans", sans-serif; color: var(--white); }

  .option-label { position: absolute; font-family: "Open Sans", sans-serif; font-size: 27px; color: var(--white); }
  .option-label--1 { left: 752px; top: 8px; }
  .option-label--2 { left: 228px; top: 698px; }
  .option-label--3 { left: 802px; top: 698px; }

  .card { position: absolute; width: 525px; height: 299px; overflow: hidden;
    background: radial-gradient(ellipse 70% 80% at 50% 45%, var(--navy-light), var(--navy) 55%, var(--navy-dark)); }
  .card--front { left: 55px; top: 55px; }
  .card--opt1 { left: 604px; top: 58px; }
  .card--opt2 { left: 55px; top: 376px; }
  .card--opt3 { left: 604px; top: 381px; }

  /* Front */
  .front-wave { position: absolute; inset: 0; }
  .doctor-name { position: absolute; top: 44px; width: 100%; text-align: center;
    font-family: "Cinzel", serif; font-size: 40px; letter-spacing: 3px; }
  .credentials { position: absolute; top: 98px; width: 100%; text-align: center;
    font-family: "Tinos", serif; font-size: 11px; letter-spacing: 1px; }
  .specialty { position: absolute; top: 141px; width: 100%; text-align: center;
    font-family: "Tinos", serif; font-size: 19px; letter-spacing: 2.4px; }
  .tagline { position: absolute; left: 124px; top: 256px;
    font-family: "Tinos", serif; font-weight: 700; font-size: 23px; }
  .guild-mark { position: absolute; left: 404px; top: 208px; width: 84px; text-align: center;
    font-family: "Tinos", serif; font-size: 8.5px; line-height: 1.2; color: var(--white); }
  .guild-mark__dot { width: 26px; height: 26px; border-radius: 50%; background: var(--gold); margin: 0 auto 4px; }

  /* Back */
  .back-footer { position: absolute; left: 0; right: 0; bottom: 0; height: 78px; background: var(--crimson);
    border-top: 3px solid var(--rule); text-align: center; font-family: "Tinos", serif; font-size: 15px; line-height: 18px; padding-top: 6px; }
  .back-footer__contact { margin-top: 7px; }
  .back-footer__divider { display: inline-block; width: 1px; height: 18px; background: var(--white); margin: 0 8px; vertical-align: -4px; }

  .guild-faint { position: absolute; text-align: center; font-family: "Tinos", serif; font-size: 15px; line-height: 1.2;
    color: rgba(255,255,255,0.07); }
  .guild-faint__dot { width: 80px; height: 80px; border-radius: 50%; background: rgba(255,255,255,0.05); margin: 0 auto 6px; }

  .hours-title { position: absolute; width: 100%; text-align: center; font-size: 20px; letter-spacing: 0.5px; }
  .hours-list { position: absolute; width: 100%; text-align: center; font-size: 15.5px; line-height: 23px; color: var(--ink-soft); }

  .card--opt1 .hours-title { top: 14px; }
  .card--opt1 .hours-list { top: 46px; }
  .card--opt1 .guild-faint { left: 300px; top: 100px; }

  .card--opt2 .hours-title { top: 44px; letter-spacing: 1.5px; }
  .card--opt2 .guild-faint { left: 170px; top: 30px; width: 180px; }
  .hours-cols { position: absolute; top: 84px; left: 0; width: 100%; display: flex; justify-content: center; font-size: 15.5px; line-height: 24px; color: var(--ink-soft); }
  .hours-cols__left { text-align: right; padding-right: 14px; width: 262px; }
  .hours-cols__right { text-align: left; padding-left: 14px; width: 263px; border-left: 1px solid rgba(255,255,255,0.7); height: 72px; }
  .hours-cols__sunday { position: absolute; top: 162px; width: 100%; text-align: center; font-size: 15.5px; }

  .card--opt3 .hours-title { top: 30px; }
  .card--opt3 .hours-title span { border-bottom: 1.5px solid var(--white); padding-bottom: 1px; letter-spacing: 1.2px; }
  .card--opt3 .hours-list { top: 74px; line-height: 29.5px; }
  .card--opt3 .guild-faint { left: 170px; top: 30px; width: 180px; }
  .pipe { margin: 0 4px; }
</style>
</head>
<body>
  <div class="option-label option-label--1">Option# 1</div>
  <div class="option-label option-label--2">Option# 2</div>
  <div class="option-label option-label--3">Option# 3</div>

  <section class="card card--front">
    <svg class="front-wave" width="525" height="299" viewBox="0 0 525 299">
      <path d="M0,228 C110,282 230,276 330,252 S470,206 525,200 L525,299 L0,299 Z" fill="var(--crimson)"/>
      <path d="M0,228 C60,250 100,262 140,270 L140,299 L0,299 Z" fill="var(--crimson-dark)" opacity="0.6"/>
      <path d="M0,222 C110,276 230,270 330,246 S470,200 525,194" fill="none" stroke="var(--navy-dark)" stroke-width="4"/>
      <path d="M0,196 C110,262 230,262 330,240 S470,196 525,188" fill="none" stroke="var(--gold)" stroke-width="4"/>
      <path d="M0,150 C60,205 150,234 250,234 S420,210 525,184" fill="none" stroke="var(--sage)" stroke-width="4"/>
    </svg>
    <h1 class="doctor-name">Dr. Orin Halvey</h1>
    <p class="credentials">M.B.B.S., F.N.G.F.H.O</p>
    <p class="specialty">Family General Practitioner</p>
    <p class="tagline">Caring about your health</p>
    <div class="guild-mark">
      <div class="guild-mark__dot"></div>
      Noble Guild of Family Healers Oceania
    </div>
  </section>

  <section class="card card--opt1">
    <div class="guild-faint"><div class="guild-faint__dot"></div>Noble Guild of<br>Family Healers</div>
    <h2 class="hours-title">Working Hours</h2>
    <div class="hours-list">
      Monday&nbsp;&nbsp; 7 am&nbsp;&nbsp; - 7 pm<br>
      Tuesday&nbsp; 7 am - 12 pm<br>
      Wednesday&nbsp; 7 am - 10 pm<br>
      Thursday&nbsp; 7 am - 12 pm<br>
      Friday&nbsp;&nbsp;&nbsp; 7 am&nbsp;&nbsp; - 8 pm<br>
      Saturday&nbsp; 8 am - 10 pm<br>
      Sunday - Off
    </div>
    <footer class="back-footer">
      Level 2, Harbour Walk, Ellery Grove Shopping Centre<br>Brindle Park, NSW 2198
      <div class="back-footer__contact">P: 02 9471 3860<span class="back-footer__divider"></span>F: 02 9471 3861</div>
    </footer>
  </section>

  <section class="card card--opt2">
    <div class="guild-faint"><div class="guild-faint__dot"></div>Noble Guild of<br>Family Healers</div>
    <h2 class="hours-title">Working Hours</h2>
    <div class="hours-cols">
      <div class="hours-cols__left">Monday&nbsp; 7 am&nbsp; - 7 pm<br>Tuesday&nbsp; 7 am - 12 pm<br>Wednesday&nbsp; 7 am - 10 pm</div>
      <div class="hours-cols__right">Thursday&nbsp; 7 am - 12 pm<br>Friday&nbsp;&nbsp;&nbsp; 7 am&nbsp;&nbsp; - 8 pm<br>Saturday&nbsp; 8 am - 10 pm</div>
    </div>
    <div class="hours-cols__sunday">Sunday - Off</div>
    <footer class="back-footer">
      Level 2, Harbour Walk, Ellery Grove Shopping Centre<br>Brindle Park, NSW 2198
      <div class="back-footer__contact">P: 02 9471 3860<span class="back-footer__divider"></span>F: 02 9471 3861</div>
    </footer>
  </section>

  <section class="card card--opt3">
    <div class="guild-faint"><div class="guild-faint__dot"></div>Noble Guild of<br>Family Healers</div>
    <h2 class="hours-title"><span>Working Hours</span></h2>
    <div class="hours-list">
      Monday&nbsp;&nbsp; 7 am&nbsp; - 7 pm<span class="pipe">|</span>Tuesday&nbsp; 7 am - 12 pm<br>
      Wednesday&nbsp; 7 am - 10 pm<span class="pipe">|</span>Thursday&nbsp; 7 am - 12 pm<br>
      Friday&nbsp;&nbsp;&nbsp; 7 am&nbsp;&nbsp; - 8 pm<span class="pipe">|</span>Saturday&nbsp; 8 am - 10 pm<br>
      Sunday - Off
    </div>
    <footer class="back-footer">
      Level 2, Harbour Walk, Ellery Grove Shopping Centre<br>Brindle Park, NSW 2198
      <div class="back-footer__contact">P: 02 9471 3860<span class="back-footer__divider"></span>F: 02 9471 3861</div>
    </footer>
  </section>
</body>
</html>
```